TRELLCor 2025 Annual Conference PPT

Need a template deck to highlight sponsors and exhibitors for an annual meeting. Most of the content will be company logos with limited text. Looking for interesting creative backgrounds. Need to incorporate the colors and logo for the meeting that have been uploaded. As well as the TRELLCor company logo. TRELLCor is a professional association for energy storage. here is a link to the meeting website https://hvm.trellcor.org/

Need 3 Major sponsor slides:
Gigawatt
Megawatt
Kilowatt

Then a different look for all other sponsors.

```html
<!DOCTYPE html>
<html lang="en">
<head>
<meta charset="utf-8">
<title>Sponsors of TRELLCor 2025 – Kilowatt Sponsors</title>
<link rel="stylesheet" href="https://fonts.googleapis.com/css2?family=Inter:wght@400;600&display=swap">
<style>
  :root {
    --navy: #040a26;
    --navy-deep: #03071c;
    --ink: #ffffff;
    --muted: #c9ccd4;
    --accent-blue: #3a86e8;
    --accent-orange: #f5a21a;
    --band-light: #a8c9d8;
    --scene-green: #1f7a3c;
    --scene-teal: #0f4a5e;
    --scene-blue: #0b2050;
  }
  * { margin: 0; padding: 0; box-sizing: border-box; }
  html, body { width: 1200px; height: 677px; overflow: hidden; background: var(--navy-deep); }
  .slide {
    position: relative;
    width: 1200px;
    height: 677px;
    overflow: hidden;
    background: radial-gradient(ellipse at 50% 55%, #0a1a44 0%, var(--navy) 55%, var(--navy-deep) 100%);
    font-family: "Inter", sans-serif;
    color: var(--ink);
  }
  .title-accent {
    position: absolute;
    left: 54px; top: 45px;
    width: 4px; height: 44px;
    background: linear-gradient(to bottom, var(--accent-blue), var(--accent-orange));
  }
  .slide-title {
    position: absolute;
    left: 70px; top: 52px;
    font-size: 23px;
    font-weight: 400;
    letter-spacing: 0.2px;
  }
  .tier-label {
    position: absolute;
    left: 70px; top: 111px;
    font-size: 23px;
    font-weight: 400;
  }
  .event-mark {
    position: absolute;
    right: 44px; top: 24px;
    font-size: 14px;
    font-weight: 400;
    letter-spacing: 1.5px;
    color: var(--muted);
    text-transform: uppercase;
  }
  .hero-art {
    position: absolute;
    left: 300px; top: 180px;
    width: 660px; height: 400px;
    border-radius: 50%;
    background: radial-gradient(ellipse at 52% 52%, var(--scene-green) 0%, var(--scene-teal) 32%, var(--scene-blue) 58%, rgba(4,10,38,0) 75%);
    opacity: 0.85;
  }
  .sponsor-list {
    position: absolute;
    left: 76px; top: 282px;
    display: flex;
    flex-direction: column;
    gap: 30px;
  }
  .sponsor-name {
    display: flex;
    align-items: center;
    gap: 12px;
    font-size: 32px;
    font-weight: 600;
    color: var(--muted);
    letter-spacing: 0.5px;
  }
  .sponsor-name.white { color: var(--ink); }
  .sponsor-dot {
    width: 38px; height: 38px;
    border-radius: 50%;
    background: var(--muted);
  }
  .bottom-band {
    position: absolute;
    left: 0; bottom: 0;
    width: 100%; height: 7px;
    background: linear-gradient(to right, var(--accent-orange) 0%, #f0b040 30%, var(--band-light) 70%, var(--accent-blue) 100%);
  }
</style>
</head>
<body>
  <main class="slide">
    <div class="title-accent"></div>
    <h1 class="slide-title">Sponsors of TRELLCor 2025</h1>
    <h2 class="tier-label">Kilowatt Sponsors</h2>
    <div class="event-mark">TRELLCor 2025</div>

    <div class="hero-art" role="img" aria-label="Electric car charging at a glowing charging station overgrown with green plants"></div>

    <section class="sponsor-list">
      <div class="sponsor-name"><span class="sponsor-dot"></span>KORVANE ENERGY</div>
      <div class="sponsor-name white">Azurel Systems</div>
    </section>

    <div class="bottom-band"></div>
  </main>
</body>
</html>
```